Silver Bloom Marisol's Cleaning Service Business Cards Project

A business card with all contact details with logo design on there (already have a logo) eye catching Logo and contact info on one side, full logo on the back, must target upper class residential and corporate companies, fitness companies, still keep it on the feminine side of things , must look elegant

Target Market(s)

Upper class homes and corporate companies

Industry/Entity Type

Cleaning Service

Contact Information for Business Card

Name: Marisol Quenby
Position: Director
ABN: 31647209853
Email: marisolssilvercleaning@tidymail.example
Number: 0417906354

Font styles to use
Decorative

Colors

Designer to choose colors to be used in the design.

Requirements
Must have
• Available Sydney Wide, contact info and logo on one side, full logo on the back
Nice to have
• Professional appearance
Should not have
• Cheap advert looking stuff

```html
<!DOCTYPE html>
<html lang="en">
<head>
<meta charset="utf-8">
<title>Silver Bloom Marisol's Cleaning Service – Business Card</title>
<link rel="stylesheet" href="https://fonts.googleapis.com/css2?family=Oswald:wght@500&family=Roboto:wght@400&family=Lora:wght@600&display=swap">
<style>
  :root {
    --backdrop: #d9dade;
    --card-white: #ffffff;
    --card-white-shade: #eef0f3;
    --navy: #2b3144;
    --navy-deep: #232838;
    --ink: #2a2f40;
    --silver: #e4e6ea;
    --ornament-light: #dfe2e8;
    --ornament-dark: #363d53;
  }
  * { box-sizing: border-box; margin: 0; padding: 0; }
  html, body { width: 1200px; height: 900px; overflow: hidden; }
  body {
    background: var(--backdrop);
    display: flex;
    flex-direction: column;
    align-items: center;
    justify-content: center;
    gap: 40px;
  }
  .card {
    position: relative;
    width: 700px;
    height: 400px;
    border-radius: 22px;
    overflow: hidden;
    box-shadow: 0 10px 28px rgba(20, 24, 36, 0.25);
  }

  /* Front */
  .card-front {
    background: linear-gradient(135deg, var(--card-white) 40%, var(--card-white-shade));
    color: var(--ink);
  }
  .ornament {
    position: absolute;
    border-radius: 60px;
    background: radial-gradient(ellipse at center, var(--ornament-light) 0%, rgba(223,226,232,0.35) 70%, rgba(223,226,232,0) 100%);
  }
  .ornament-top-left { left: 150px; top: 8px; width: 200px; height: 120px; }
  .ornament-mid-left { left: -10px; top: 150px; width: 220px; height: 120px; }
  .ornament-top-right { right: 10px; top: 40px; width: 230px; height: 130px; }
  .ornament-bottom { left: 380px; bottom: 6px; width: 240px; height: 120px; }

  .identity {
    position: absolute;
    left: 60px;
    top: 170px;
    width: 270px;
    text-align: right;
  }
  .identity-name {
    font-family: "Oswald", sans-serif;
    font-weight: 500;
    font-size: 36px;
    letter-spacing: 1px;
    text-transform: uppercase;
    line-height: 1;
  }
  .identity-role {
    font-family: "Roboto", sans-serif;
    font-size: 14px;
    margin-top: 6px;
  }
  .divider {
    position: absolute;
    left: 350px;
    top: 110px;
    width: 2px;
    height: 200px;
    background: var(--ink);
  }
  .contact {
    position: absolute;
    left: 372px;
    top: 176px;
    list-style: none;
    font-family: "Roboto", sans-serif;
    font-size: 14px;
    line-height: 26px;
  }
  .contact li { display: flex; align-items: center; gap: 8px; }
  .contact svg { width: 12px; height: 12px; flex: none; }
  .contact-abn { padding-left: 0; }

  /* Back */
  .card-back {
    background: var(--navy);
    color: var(--silver);
    display: flex;
    flex-direction: column;
    align-items: center;
    justify-content: center;
  }
  .pattern {
    position: absolute;
    border-radius: 80px;
    background: radial-gradient(ellipse at center, var(--ornament-dark) 0%, rgba(54,61,83,0) 75%);
  }
  .pattern-a { left: -40px; top: -30px; width: 320px; height: 200px; }
  .pattern-b { right: -40px; bottom: -30px; width: 340px; height: 210px; }
  .pattern-c { left: 200px; top: 40px; width: 300px; height: 110px; }
  .brand {
    position: relative;
    text-align: center;
    font-family: "Lora", serif;
    font-weight: 600;
    color: var(--silver);
  }
  .brand-mark {
    width: 70px;
    height: 70px;
    border-radius: 50%;
    border: 2px solid var(--silver);
    margin: 0 auto 22px;
  }
  .brand-name {
    font-size: 46px;
    letter-spacing: 2px;
    text-transform: uppercase;
    line-height: 1;
  }
  .brand-tagline {
    font-size: 15px;
    letter-spacing: 5px;
    text-transform: uppercase;
    margin-top: 12px;
  }
</style>
</head>
<body>

<section class="card card-front">
  <div class="ornament ornament-top-left" role="img" aria-label="Flowing floral scroll ornament"></div>
  <div class="ornament ornament-mid-left" role="img" aria-label="Flowing floral scroll ornament"></div>
  <div class="ornament ornament-top-right" role="img" aria-label="Flowing floral scroll ornament"></div>
  <div class="ornament ornament-bottom" role="img" aria-label="Flowing floral scroll ornament"></div>

  <div class="identity">
    <h1 class="identity-name">Marisol Quenby</h1>
    <p class="identity-role">Director</p>
  </div>

  <div class="divider"></div>

  <ul class="contact">
    <li class="contact-abn">ABN: 31647209853</li>
    <li>
      <svg viewBox="0 0 12 12" aria-hidden="true"><path d="M3 1 L5 3.5 L4 5 Q5 7 7 8 L8.5 7 L11 9 L9.5 11 Q5 10.5 1 3 Z" fill="currentColor"/></svg>
      0417906354
    </li>
    <li>
      <svg viewBox="0 0 12 12" aria-hidden="true"><rect x="1" y="2.5" width="10" height="7" fill="none" stroke="currentColor" stroke-width="1.2"/><path d="M1 2.5 L6 6.5 L11 2.5" fill="none" stroke="currentColor" stroke-width="1.2"/></svg>
      marisolssilvercleaning@tidymail.example
    </li>
  </ul>
</section>

<section class="card card-back">
  <div class="pattern pattern-a" role="img" aria-label="Faint floral scroll pattern"></div>
  <div class="pattern pattern-b" role="img" aria-label="Faint floral scroll pattern"></div>
  <div class="pattern pattern-c" role="img" aria-label="Faint floral scroll ornament above the name"></div>
  <div class="brand">
    <div class="brand-mark"></div>
    <p class="brand-name">Silver Bloom</p>
    <p class="brand-tagline">Marisol's Cleaning Service</p>
  </div>
</section>

</body>
</html>
```